Family Values Statement Image

I have created a statement of values for my family. Our last name is Pilwothy, and we are using those letters as an acronym. I would like an image with these words and letters with a tree with deep roots, where the roots are the focal point.

A - All In
N - Never Settle
D - Dependable
E - Enthusiastic
R - Repair
E - Enduring
G - Gushy Hearted
G - Gratitudes

Note that "gratitudes" is intentionally misspelled.

• On further reflection, I am interested in the words being much more prominent than the tree. In fact, the tree could be quite small or even just a watermark behind the words.

```html
<!DOCTYPE html>
<html lang="en">
<head>
<meta charset="utf-8">
<title>Our Family Values – Pilwothy</title>
<link rel="stylesheet" href="https://fonts.googleapis.com/css2?family=Inter:wght@500;800&display=swap">
<style>
  :root {
    --paper: #f1f0ee;
    --ink: #3b3b3b;
    --ink-soft: #5a5a5a;
    --leaf: #c4c4c4;
    --trunk: #4a4a4a;
  }
  html, body {
    margin: 0;
    padding: 0;
    width: 1122px;
    height: 1200px;
    overflow: hidden;
    background: var(--paper);
  }
  .poster {
    position: relative;
    width: 1122px;
    height: 1200px;
    background: var(--paper);
    font-family: "Inter", Arial, sans-serif;
    color: var(--ink);
  }
  .tree-art {
    position: absolute;
    left: 0;
    top: 0;
    width: 1122px;
    height: 660px;
  }
  .value {
    position: absolute;
    margin: 0;
    font-weight: 800;
    letter-spacing: -0.02em;
    white-space: nowrap;
    line-height: 1;
    transform-origin: center center;
  }
  .value--all-in      { left: 107px; top: 687px; font-size: 34px; transform: translate(-50%, -50%) rotate(-20deg); }
  .value--never       { left: 172px; top: 752px; font-size: 36px; transform: translate(-50%, -50%) rotate(-45deg); }
  .value--dependable  { left: 234px; top: 826px; font-size: 54px; transform: translate(-50%, -50%) rotate(-60deg); }
  .value--enthusiastic{ left: 400px; top: 824px; font-size: 38px; transform: translate(-50%, -50%) rotate(-80deg); }
  .value--repair      { left: 566px; top: 788px; font-size: 52px; transform: translate(-50%, -50%) rotate(-88deg); }
  .value--enduring    { left: 730px; top: 826px; font-size: 56px; transform: translate(-50%, -50%) rotate(-88deg); }
  .value--gushy       { left: 860px; top: 880px; font-size: 56px; transform: translate(-50%, -50%) rotate(-87deg); }
  .value--gratitudes  { left: 950px; top: 766px; font-size: 38px; transform: translate(-50%, -50%) rotate(-84deg); }

  .signature {
    position: absolute;
    left: 508px;
    top: 1058px;
    transform: translateX(-50%);
    text-align: center;
  }
  .signature__label {
    margin: 0;
    font-size: 15px;
    font-weight: 500;
    letter-spacing: 0.22em;
    color: var(--ink-soft);
  }
  .signature__name {
    margin: 4px 0 0;
    font-size: 72px;
    font-weight: 800;
    letter-spacing: -0.02em;
    line-height: 1;
  }
</style>
</head>
<body>
<main class="poster">
  <svg class="tree-art" viewBox="0 0 1122 660" role="img" aria-label="Illustration of a broad grey tree with leafy branches and deep spreading roots">
    <defs>
      <linearGradient id="treeTone" x1="0" y1="0" x2="0" y2="1">
        <stop offset="0" stop-color="var(--leaf)"/>
        <stop offset="0.45" stop-color="#9a9a9a"/>
        <stop offset="1" stop-color="var(--trunk)"/>
      </linearGradient>
    </defs>
    <rect x="0" y="0" width="1122" height="660" fill="url(#treeTone)" opacity="0.55"/>
  </svg>

  <ul style="list-style:none;margin:0;padding:0;">
    <li class="value value--all-in">All In</li>
    <li class="value value--never">Never Settle</li>
    <li class="value value--dependable">Dependable</li>
    <li class="value value--enthusiastic">Enthusiastic</li>
    <li class="value value--repair">Repair</li>
    <li class="value value--enduring">Enduring</li>
    <li class="value value--gushy">Gushy Hearted</li>
    <li class="value value--gratitudes">Graditudes</li>
  </ul>

  <header class="signature">
    <p class="signature__label">OUR FAMILY VALUES</p>
    <h1 class="signature__name">Pilwothy</h1>
  </header>
</main>
</body>
</html>
```